Landingpage design

We need a landingpage for a Chatterloom add campaign. We sell socks made of bamboo in super quality. Our customers loves us, and we have a 5 heart rating at scorevane.com.

We want to create a add campaign targeted new customers, and the offer is that they can buy 1 pair of bamboo socks as a test, for only 20 DKK (2,7 Euro) including shipment. Our webpage is www.tuvelo.dk, landingpage should be built i Kyvio, a wysiwyg editor. based on their template. like:
https://tuvelo.pemlorsite.com/13844-sales-page
https://tuvelo.pemlorsite.com/13696-sales-page
https://tuvelo.pemlorsite.com/13845-sales-page

You don't have to follow the templates 100% if you have better ideas. We have an account for snapvaultly, so please get stockphotos from here.

Bamboo socks has a lot of great selling points, you can see a good desciption here:
https://feltrano.com/us/why-bamboo

We expect you to have experience in landingpage design, and expect to end up with 2 landingpages we can splittest on.

This is the first of a number of landingpages we need in the future, so for the right person there will be plenty of more work.

Target Market(s)

Denmark

Industry/Entity Type

E-Commerce

Number of Pages Required

2 page

Colors

Designer to choose colors to be used in the design.

Requirements
Must have
• A great selling page, showing all the great things with bamboo socks. It should be supplied with good packshots from snapvaultly.com

```html
<!DOCTYPE html>
<html lang="en">
<head>
<meta charset="utf-8">
<title>Tuvelo – Bamboo Socks Landing Page</title>
<link href="https://fonts.googleapis.com/css2?family=Roboto:wght@300;400;500;700&display=swap" rel="stylesheet">
<style>
:root{
  --green:#2fae7d;
  --ink:#232a33;
  --text:#5d6670;
  --muted:#9aa1a8;
  --mint:#e8f3ec;
  --white:#ffffff;
  --footer:#1f2531;
  --star:#f2b01e;
}
*{box-sizing:border-box;margin:0;padding:0}
html,body{width:1200px;height:5099px;overflow:hidden}
body{font-family:'Roboto',sans-serif;color:var(--text);background:var(--white);position:relative}
section,header,footer{position:absolute;left:0;width:1200px}
.btn{display:inline-block;font-size:13px;font-weight:500;letter-spacing:.5px;text-transform:uppercase;padding:0 30px;height:34px;line-height:34px;border-radius:2px;text-align:center}
.btn-solid{background:var(--green);color:var(--white)}
.btn-ghost{border:1px solid var(--green);color:var(--green);background:var(--white)}
.photo{position:absolute}
/* header */
.site-header{top:0;height:68px;background:var(--white)}
.brand{position:absolute;left:132px;top:14px;display:flex;align-items:center;gap:10px}
.brand-square{width:40px;height:40px;background:var(--ink)}
.brand-name{font-size:14px;font-weight:500;color:var(--ink)}
.nav{position:absolute;left:485px;top:24px;display:flex;gap:38px;font-size:12px;text-transform:uppercase;color:var(--text)}
.nav .active{color:var(--ink);border-bottom:2px solid var(--green);padding-bottom:4px}
.site-header .btn{position:absolute;left:908px;top:18px;width:160px;height:30px;line-height:30px;font-size:11px}
/* hero */
.hero{top:68px;height:493px;background:linear-gradient(90deg,#f0f0f0,#e6e6e6)}
.hero-copy{position:absolute;left:134px;top:104px;width:640px}
.hero-title{font-size:38px;line-height:1.2;font-weight:700;color:var(--ink)}
.ticks{list-style:none;margin-top:20px}
.ticks li{font-size:14px;line-height:28px;color:var(--text);display:flex;align-items:center;gap:10px}
.ticks svg{width:14px;height:14px;flex:none}
.hero-actions{margin-top:22px;display:flex;gap:22px}
.hero-actions .btn{width:190px}
.note{font-size:11px;color:var(--muted);margin-top:10px}
.hero-photo{left:760px;top:20px;width:400px;height:473px;background:linear-gradient(160deg,#dcdcdc,#c9c7c4 55%,#3a3a3a)}
/* why */
.why{top:561px;height:588px;background:var(--green);color:var(--white);text-align:center}
.why h2{font-size:34px;font-weight:500;margin-top:95px}
.rule{width:60px;height:2px;background:var(--white);margin:12px auto 0}
.why .lead{font-size:15px;line-height:1.6;width:620px;margin:26px auto 0}
.why-cards{position:absolute;left:135px;top:270px;display:flex;gap:22px}
.why-card{width:216px;height:196px;background:var(--white);color:var(--text);padding:30px 20px}
.why-card svg{width:34px;height:34px}
.why-card h3{font-size:17px;font-weight:500;color:var(--ink);margin:12px 0 8px}
.why-card p{font-size:11px;line-height:1.5;color:var(--muted)}
/* feature rows */
.feature{height:330px;background:var(--white)}
.feature .photo{top:0;width:600px;height:100%}
.feature-text{position:absolute;top:90px;width:420px}
.feature h2{font-size:28px;font-weight:700;color:var(--ink)}
.feature p{font-size:15px;line-height:1.7;margin-top:18px}
.f-clean{top:1149px;height:323px}
.f-clean .photo{left:0;background:linear-gradient(135deg,#d8dde0,#9aa3a8 60%,#c45bb0)}
.f-clean .feature-text{left:648px}
.f-strong{top:1472px}
.f-strong .photo{left:600px;background:linear-gradient(160deg,#5a6068,#2b2f36)}
.f-strong .feature-text{left:134px}
.f-water{top:1802px}
.f-water .photo{left:0;background:linear-gradient(135deg,#f4f4f4,#d7dcdf 60%,#3b3b3b)}
.f-water .feature-text{left:648px}
/* discount */
.discount{top:2132px;height:204px;background:var(--mint)}
.discount .big{position:absolute;left:132px;top:60px;font-size:70px;font-weight:700;color:var(--green)}
.discount h2{position:absolute;left:352px;top:70px;font-size:24px;font-weight:500;color:var(--ink);line-height:1.3;width:430px}
.discount .btn{position:absolute;left:872px;top:72px;width:196px}
.discount .note{position:absolute;left:966px;top:112px}
/* facts */
.facts{top:2336px;height:554px;background:linear-gradient(180deg,#7fd5e8,#3f8cf0);color:var(--white);text-align:center}
.facts h2{font-size:34px;font-weight:500;margin-top:95px}
.facts .lead{font-size:15px;line-height:1.6;width:560px;margin:26px auto 0}
.fact-list{position:absolute;left:150px;top:280px;display:flex;gap:40px}
.fact{width:273px}
.fact .icon{width:84px;height:84px;border-radius:50%;background:var(--white);margin:0 auto;display:flex;align-items:center;justify-content:center}
.fact p{font-size:14px;line-height:1.6;margin-top:22px}
/* video */
.video{top:2890px;height:731px;background:var(--white);text-align:center}
.video h2{font-size:32px;font-weight:500;color:var(--ink);margin-top:95px}
.video .lead{font-size:14px;line-height:1.6;width:620px;margin:22px auto 0}
.video .photo{left:290px;top:282px;width:620px;height:340px;background:linear-gradient(135deg,#6b4a35,#3a2a20 55%,#8a6a4d)}
.play{position:absolute;left:570px;top:422px;width:60px;height:60px}
.leaf{position:absolute}
.leaf-tl{left:0;top:0;width:250px;height:200px;background:linear-gradient(135deg,#4f7a3a,#a9c79a);opacity:.35}
.leaf-br{right:0;bottom:30px;width:200px;height:320px;background:linear-gradient(200deg,#5c8a45,#b6d3a6);opacity:.35}
/* rating */
.rating{top:3621px;height:792px;background:var(--white);text-align:center}
.stars{margin-top:92px;display:flex;justify-content:center;gap:4px}
.rating h2{font-size:34px;font-weight:500;color:var(--ink);margin-top:12px}
.rating .lead{font-size:14px;line-height:1.6;width:420px;margin:22px auto 0}
.reviews{position:absolute;left:136px;top:328px;display:flex;gap:42px}
.review{width:297px;height:290px;background:#f1f1f1;text-align:left;padding:28px 30px}
.review-head{display:flex;align-items:center;gap:12px}
.avatar{width:36px;height:36px;border-radius:50%;background:#c3c8cc}
.review-name{font-size:14px;color:var(--ink)}
.review-stars{color:var(--star);font-size:13px}
.review p{font-size:13px;line-height:1.6;margin-top:20px}
.arrow{position:absolute;top:460px;width:14px;height:20px}
.arrow-l{left:102px}.arrow-r{left:1082px}
.rating .btn{position:absolute;left:486px;top:652px;width:228px}
/* bottom hero */
.hero-bottom{top:4413px;height:442px;background:linear-gradient(90deg,#f0f0f0,#e8e8e8)}
.hero-bottom .hero-copy{top:70px;width:600px}
.hero-bottom-photo{left:760px;top:0;width:400px;height:442px;background:linear-gradient(160deg,#ececec,#e6a39a 55%,#c9a27c)}
/* footer */
.site-footer{top:4855px;height:244px;background:var(--footer);color:#c9ccd2}
.f-col{position:absolute;top:60px;font-size:12px;line-height:1.6}
.f-col h4{font-size:16px;font-weight:500;color:var(--white);margin-bottom:14px}
.f-col a{color:var(--green);text-decoration:none}
.f-about{left:132px;width:220px}
.f-contact{left:450px;width:230px}
.f-nav{left:768px}
.social{margin-top:8px;display:flex;align-items:center;gap:6px;font-size:12px;color:var(--white)}
.social-dot{width:14px;height:14px;border-radius:50%;background:var(--white)}
</style>
</head>
<body>

<header class="site-header">
  <div class="brand"><span class="brand-square"></span><span class="brand-name">Tuvelo</span></div>
  <nav class="nav"><span class="active">Home</span><span>Why Bamboo</span><span>About Us</span><span>Reviews</span></nav>
  <span class="btn btn-solid">Buy Now</span>
</header>

<section class="hero">
  <div class="hero-copy">
    <h1 class="hero-title">Enjoy Your First Pair of Bamboo Socks for Only 20 PKK</h1>
    <ul class="ticks">
      <li><svg viewBox="0 0 14 14"><path d="M2 7l3 3 7-7" fill="none" stroke="#2fae7d" stroke-width="2"/></svg>We have been working on textile for more than 10 years</li>
      <li><svg viewBox="0 0 14 14"><path d="M2 7l3 3 7-7" fill="none" stroke="#2fae7d" stroke-width="2"/></svg>All products meet our high quality standards</li>
      <li><svg viewBox="0 0 14 14"><path d="M2 7l3 3 7-7" fill="none" stroke="#2fae7d" stroke-width="2"/></svg>Our customers loves us, and we have a 5 stars rating at scorevane.com</li>
    </ul>
    <div class="hero-actions"><span class="btn btn-solid">Buy Now</span><span class="btn btn-ghost">&#9654;&nbsp; Watch Video</span></div>
    <p class="note">Shipment included</p>
  </div>
  <div class="photo hero-photo" role="img" aria-label="Woman in grey sweater and black bamboo socks sitting on the floor"></div>
</section>

<section class="why">
  <h2>Why Bamboo Clothing?</h2>
  <div class="rule"></div>
  <p class="lead">It was only in 2011 that the University of Norvale discovered how you can make fabric from bamboo stems. Now bamboo has the potential to become the textile of the future.</p>
  <div class="why-cards">
    <div class="why-card"><svg viewBox="0 0 34 34"><path d="M11 5l-7 5 3 5 3-2v16h14V13l3 2 3-5-7-5c-1 3-3 4-5 4s-4-1-5-4z" fill="none" stroke="#2fae7d" stroke-width="2"/></svg><h3>Comfortable</h3><p>Bamboo fabric breathes, keeping you comfortable in garments made of it.</p></div>
    <div class="why-card"><svg viewBox="0 0 34 34"><path d="M6 28C6 14 16 6 28 6c0 12-8 22-22 22zM6 28L20 14" fill="none" stroke="#2fae7d" stroke-width="2"/></svg><h3>Eco-friendly</h3><p>Bamboo is a very fast growing, natural plant and needs no pesticides at all.</p></div>
    <div class="why-card"><svg viewBox="0 0 34 34"><path d="M8 10h18v6H8zM6 16h22l-3 12H9z" fill="none" stroke="#2fae7d" stroke-width="2"/></svg><h3>Exquisitely soft</h3><p>The moment you wear it, you feel the difference against other fabrics.</p></div>
    <div class="why-card"><svg viewBox="0 0 34 34"><path d="M17 4l11 24H6z M12 20h10" fill="none" stroke="#2fae7d" stroke-width="2"/></svg><h3>Thermo-control</h3><p>Bamboo fabric is warm in winter and cool and fresh in summer.</p></div>
  </div>
</section>

<section class="feature f-clean">
  <div class="photo" role="img" aria-label="Woman with shopping bags wearing knee-high bamboo socks"></div>
  <div class="feature-text"><h2>Completely Clean</h2><p>Bamboo fibers doesnt under go much chemical processing to make the fabric, so you can easily wear it without causing any allergic irritation to the skin that is more prevalent with heavily processed fabrics.</p></div>
</section>

<section class="feature f-strong">
  <div class="feature-text"><h2>Strong Material</h2><p>Bamboo fabric is lightweight yet strong. The natural processing of fibre bamboo allows the fibre to remain strong to produce an extremely high quality product. This process gives a material that is very durable.</p></div>
  <div class="photo" role="img" aria-label="Close-up of legs in black socks and leather shoes on a bed"></div>
</section>

<section class="feature f-water">
  <div class="photo" role="img" aria-label="Woman in bright glass corridor wearing black bamboo socks"></div>
  <div class="feature-text"><h2>Water Absorbent</h2><p>Bamboo fibers are water absorbent. So if you live in a humid environment this is the fabric for you. Think of the sweat it will absorb and evaporate out of your body.</p></div>
</section>

<section class="discount">
  <span class="big">-90%</span>
  <h2>Get Your First Pair of Socks With an Exclusive Discount</h2>
  <span class="btn btn-solid">Buy Now</span>
  <span class="note">Shipment included</span>
</section>

<section class="facts">
  <h2>A Few Facts About Tuvelo</h2>
  <div class="rule"></div>
  <p class="lead">We have been working on textile for more than 10 years. This ensures that all products meet our high quality standards.</p>
  <div class="fact-list">
    <div class="fact"><div class="icon"><svg width="36" height="36" viewBox="0 0 34 34"><path d="M11 5l-7 5 3 5 3-2v16h14V13l3 2 3-5-7-5c-1 3-3 4-5 4s-4-1-5-4z" fill="#4aa3ee"/></svg></div><p>Our mission is to give our customers access to quality products at a reasonable price.</p></div>
    <div class="fact"><div class="icon"><svg width="36" height="36" viewBox="0 0 34 34"><rect x="6" y="4" width="22" height="26" rx="2" fill="#4aa3ee"/><path d="M11 12h12M11 18h12M11 24h8" stroke="#fff" stroke-width="2"/></svg></div><p>We know that the properties of bamboo are absolutely amazing and can induce, for example, sweaty and sour toes.</p></div>
    <div class="fact"><div class="icon"><svg width="36" height="36" viewBox="0 0 34 34"><circle cx="17" cy="13" r="9" fill="#4aa3ee"/><path d="M11 20l-3 11 9-4 9 4-3-11" fill="#4aa3ee"/></svg></div><p>We shop directly with the factories. This ensures the highest quality at a competitive price.</p></div>
  </div>
</section>

<section class="video">
  <div class="leaf leaf-tl" role="img" aria-label="Green leaves decoration"></div>
  <div class="leaf leaf-br" role="img" aria-label="Green leaves decoration"></div>
  <h2>A Short Video About Our Work</h2>
  <p class="lead">We sell stockings, t-shirts, sweaters and mens boxershorts. If you choose our subscription service, the products will come to you automatically.</p>
  <div class="photo" role="img" aria-label="Video still of folded clothes and socks laid out on a wooden floor"></div>
  <svg class="play" viewBox="0 0 60 60"><circle cx="30" cy="30" r="30" fill="#2fae7d"/><path d="M24 18l18 12-18 12z" fill="#fff"/></svg>
</section>

<section class="rating">
  <div class="stars">
    <svg width="28" height="28" viewBox="0 0 24 24"><path d="M12 2l3 7 7 .6-5.4 4.7 1.7 7.2L12 17.8 5.7 21.5l1.7-7.2L2 9.6 9 9z" fill="#f2b01e"/></svg>
    <svg width="28" height="28" viewBox="0 0 24 24"><path d="M12 2l3 7 7 .6-5.4 4.7 1.7 7.2L12 17.8 5.7 21.5l1.7-7.2L2 9.6 9 9z" fill="#f2b01e"/></svg>
    <svg width="28" height="28" viewBox="0 0 24 24"><path d="M12 2l3 7 7 .6-5.4 4.7 1.7 7.2L12 17.8 5.7 21.5l1.7-7.2L2 9.6 9 9z" fill="#f2b01e"/></svg>
    <svg width="28" height="28" viewBox="0 0 24 24"><path d="M12 2l3 7 7 .6-5.4 4.7 1.7 7.2L12 17.8 5.7 21.5l1.7-7.2L2 9.6 9 9z" fill="#f2b01e"/></svg>
    <svg width="28" height="28" viewBox="0 0 24 24"><path d="M12 2l3 7 7 .6-5.4 4.7 1.7 7.2L12 17.8 5.7 21.5l1.7-7.2L2 9.6 9 9z" fill="#f2b01e"/></svg>
  </div>
  <h2>We Have a 5 Stars Rating</h2>
  <p class="lead">You're in a good company. Here are some important facts and testimonials about us.</p>
  <svg class="arrow arrow-l" viewBox="0 0 14 20"><path d="M11 2L3 10l8 8" fill="none" stroke="#2fae7d" stroke-width="3"/></svg>
  <div class="reviews">
    <div class="review"><div class="review-head"><span class="avatar"></span><div><div class="review-name">Rolf Anker</div><div class="review-stars">★★★★★</div></div></div><p>Lorem ipsum dolor sit amet, consetetur sadipscing elitr, sed diam nonumy eirmod tempor invidunt ut labore et dolore magna aliquyam erat, sed diam voluptua. At vero eos et accusam et justo duo.</p></div>
    <div class="review"><div class="review-head"><span class="avatar"></span><div><div class="review-name">Rolf Anker</div><div class="review-stars">★★★★★</div></div></div><p>Lorem ipsum dolor sit amet, consetetur sadipscing elitr, sed diam nonumy eirmod tempor invidunt ut labore et dolore magna aliquyam erat, sed diam voluptua. At vero eos et accusam et justo duo.</p></div>
    <div class="review"><div class="review-head"><span class="avatar"></span><div><div class="review-name">Rolf Anker</div><div class="review-stars">★★★★★</div></div></div><p>Lorem ipsum dolor sit amet, consetetur sadipscing elitr, sed diam nonumy eirmod tempor invidunt ut labore et dolore magna aliquyam erat, sed diam voluptua. At vero eos et accusam et justo duo.</p></div>
  </div>
  <svg class="arrow arrow-r" viewBox="0 0 14 20"><path d="M3 2l8 8-8 8" fill="none" stroke="#2fae7d" stroke-width="3"/></svg>
  <span class="btn btn-solid">More Reviews</span>
</section>

<section class="hero-bottom">
  <div class="hero-copy">
    <h2 class="hero-title">Get Your First Pair of Bamboo Socks for Only 20 PKK</h2>
    <ul class="ticks">
      <li><svg viewBox="0 0 14 14"><path d="M2 7l3 3 7-7" fill="none" stroke="#2fae7d" stroke-width="2"/></svg>Powerfully insulating - keeps you cooler in summer and warmer in winter</li>
      <li><svg viewBox="0 0 14 14"><path d="M2 7l3 3 7-7" fill="none" stroke="#2fae7d" stroke-width="2"/></svg>Antibacterial - keeps your odor free and feeling and smelling fresh</li>
      <li><svg viewBox="0 0 14 14"><path d="M2 7l3 3 7-7" fill="none" stroke="#2fae7d" stroke-width="2"/></svg>Most eco-friendly fabric on the planet - help save your planet</li>
    </ul>
    <div class="hero-actions"><span class="btn btn-solid">Buy Now</span></div>
    <p class="note">Shipment included</p>
  </div>
  <div class="photo hero-bottom-photo" role="img" aria-label="Woman in pink knit sweater and hat holding a paper shopping bag"></div>
</section>

<footer class="site-footer">
  <div class="f-col f-about"><h4>About us</h4><p>At Tuvelo.dk we specialize in basic products in bamboo. We sell stockings, t-shirts, sweaters and mens boxershorts.</p><div class="social"><span class="social-dot"></span>Chatterloom</div></div>
  <div class="f-col f-contact"><h4>Contact us</h4><p>Any questions? Then e-mail <a>info@tuvelo.dk</a><br>or call us at +45 60 00 12 34<br><br>Or send us a letter to Tuvelo<br>Skovgade 8<br>4820 Lindholt</p></div>
  <div class="f-col f-nav"><h4>Navigation</h4><p>Home &nbsp;|&nbsp; Why Bamboo &nbsp;|&nbsp; About &nbsp;|&nbsp; Reviews</p></div>
</footer>

</body>
</html>
```